Wordpress theme website for professionals working together

My partner and I are offering business services, my wife in the energy business as mainly as member of the board of commissioners. I am working as interim manager/consultant in the accounting and finance area. Both activities are connected in one company VELMOT BV (dutch ltd). We need a CV based website. Beside this we do some financial and accounting services.

Target Market(s)

small medium business

Font styles to use
Sans Serif

Colors

Designer to choose colors to be used in the design.

Requirements
Must have
• Pictures of both members.
• CLEAN AND SIMPLE
• I LIKE BLACK & WHITE
Nice to have
• I like design like this theme: http://theme.pruxelo-example.com/resume/

```html
<!DOCTYPE html>
<html lang="en">
<head>
<meta charset="utf-8">
<title>VELMOT BV — Pieter, Advisor KLR</title>
<link href="https://fonts.googleapis.com/css2?family=Montserrat:wght@400;500;600;700&family=Open+Sans:wght@400;600;700&display=swap" rel="stylesheet">
<style>
:root{
  --ink:#1f1f1f;
  --dark:#2a2a2a;
  --band:#2b2b2b;
  --text:#555;
  --muted:#8a8a8a;
  --line:#d8d8d8;
  --soft:#f1f1f1;
  --paper:#fff;
  --track:#c9c9c9;
}
*{margin:0;padding:0;box-sizing:border-box}
html,body{width:1200px;height:4569px;overflow:hidden;background:var(--paper)}
body{position:relative;font-family:"Open Sans",Arial,sans-serif;color:var(--text)}
.abs{position:absolute}
h1,h2,h3,h4,.heading{font-family:"Montserrat",Arial,sans-serif;color:var(--ink)}
.section-title{position:absolute;left:0;width:1200px;text-align:center;font-size:28px;font-weight:500;letter-spacing:1px}
.lead{position:absolute;left:0;width:1200px;text-align:center;font-size:13px;line-height:27px}
.btn{position:absolute;background:var(--ink);color:#fff;font-family:"Montserrat",Arial,sans-serif;font-size:13px;font-weight:600;display:flex;align-items:center;justify-content:center}

/* header */
.site-header{position:absolute;left:0;top:0;width:1200px;height:128px;background:#fff}
.logo{position:absolute;display:flex;align-items:center;gap:10px;font-family:"Montserrat",Arial,sans-serif;font-weight:700;font-size:26px;color:var(--ink)}
.logo .mark{width:14px;height:14px;background:var(--ink)}
.nav{position:absolute;left:478px;top:52px;display:flex;gap:18px;font-family:"Montserrat",Arial,sans-serif;font-size:14px;color:var(--ink);font-weight:500}

/* hero */
.hero{position:absolute;left:0;top:128px;width:1200px;height:518px;background:linear-gradient(90deg,#e9e9e9,#d2d2d2)}
.hero-photo{position:absolute;left:580px;top:0;width:620px;height:518px;background:linear-gradient(120deg,#bdbdbd,#6d6d6d 60%,#2f2f2f)}
.hero-title{position:absolute;left:113px;top:118px;font-size:80px;font-weight:700;letter-spacing:2px}
.hero-intro{position:absolute;left:113px;top:222px;font-size:20px;line-height:34px;color:#444;width:460px}
.signature{position:absolute;left:113px;top:334px;width:90px;height:34px;background:linear-gradient(90deg,#cfcfcf,#bdbdbd)}

/* personal */
.info-card{position:absolute;left:140px;top:832px;width:892px;height:283px;background:#fff;box-shadow:0 2px 14px rgba(0,0,0,.18)}
.card-title{position:absolute;font-size:17px;font-weight:600}
.story{position:absolute;left:76px;top:72px;width:390px;font-size:12.5px;line-height:27px}
.info-row{position:absolute;left:542px;font-size:12.5px;color:var(--ink)}
.info-row span{position:absolute;left:104px;white-space:nowrap;color:var(--text)}
.dots{position:absolute;left:542px;top:246px;display:flex;gap:12px}
.dots i{width:10px;height:10px;border-radius:50%;background:var(--ink)}

/* job */
.job{position:absolute;left:0;top:1203px;width:1200px;height:427px;background:linear-gradient(135deg,#333 0%,#222 50%,#2e2e2e 100%)}
.job .section-title,.job .lead,.job-text{color:#fff}
.job-icon{position:absolute}
.job-text{position:absolute;font-size:13px;line-height:27px}
.job-text strong{font-family:"Montserrat",Arial,sans-serif;font-weight:700;font-size:13px}

/* skills */
.skills-title{position:absolute;left:113px;top:1704px;font-size:28px;font-weight:500}
.skills-copy{position:absolute;left:113px;width:420px;font-size:12px;line-height:22px;color:var(--muted)}
.skill{position:absolute;left:661px;width:360px;height:38px}
.skill label{font-size:11px;color:var(--ink);position:absolute;top:0}
.skill .track{position:absolute;top:20px;left:0;width:360px;height:6px;background:var(--track)}
.skill .fill{position:absolute;top:0;left:0;height:6px;background:var(--ink)}
.skill .tag{position:absolute;top:-12px;height:11px;padding:0 4px;background:var(--ink);color:#fff;font-size:8px;line-height:11px}

/* experience */
.experience{position:absolute;left:0;top:2026px;width:1200px;height:1020px;background:linear-gradient(160deg,#f6f6f6,#ececec 55%,#f4f4f4)}
.exp-row{position:absolute;height:146px;background:#fff}
.exp-copy{position:absolute;width:370px;font-size:12px;line-height:20px;color:var(--text)}
.exp-head{position:absolute;width:300px}
.exp-head h4{font-size:22px;font-weight:600;letter-spacing:.5px}
.exp-head p{font-family:"Montserrat",Arial,sans-serif;font-weight:700;color:var(--ink);font-size:14px;line-height:26px;margin-top:8px}
.timeline{position:absolute;left:614px;top:2231px;width:2px;height:570px;background:#999}
.dot{position:absolute;width:24px;height:24px;border-radius:50%;background:var(--dark);color:#fff;font-size:11px;display:flex;align-items:center;justify-content:center}

/* partner */
.partner{position:absolute;left:0;top:3046px;width:1200px;height:451px;background:linear-gradient(135deg,#f3f3f3,#e8e8e8)}
.partner-photo{position:absolute;left:177px;top:82px;width:248px;height:248px;border-radius:50%;background:radial-gradient(circle at 50% 40%,#bbb,#6a6a6a 70%,#3c3c3c);border:4px solid #fff}

/* portfolio */
.folio{position:absolute;top:3640px;width:235px;height:235px}
.arrow{position:absolute;top:3749px}

/* work */
.work{position:absolute;left:0;top:3975px;width:1200px;height:259px;background:linear-gradient(135deg,#2a2a2a,#1e1e1e)}
.work *{color:#fff}

/* footer */
.foot-title{position:absolute;font-size:16px;font-weight:700}
.foot-list{position:absolute;list-style:none;font-size:12.5px;color:var(--ink);line-height:27px}
.foot-list li{display:flex;align-items:center;gap:8px}
.foot-list .pip{width:8px;height:8px;border-radius:50%;background:var(--ink)}
.input{position:absolute;left:798px;top:4322px;width:287px;height:43px;border:1px solid var(--ink);font-size:11px;color:var(--ink);padding:0 12px;display:flex;align-items:center}
.rule{position:absolute;left:113px;top:4493px;width:974px;height:1px;background:var(--line)}
.copyright{position:absolute;left:0;top:4518px;width:1200px;text-align:center;font-size:12px;color:var(--ink)}
</style>
</head>
<body>

<header class="site-header">
  <div class="logo" style="left:113px;top:46px"><span>VELMOT</span><span class="mark"></span></div>
  <nav class="nav"><span>HOME</span><span>ABOUT ME</span><span>PORTFOLIO</span><span>TESTIMONIAL</span><span>CONTACT US</span></nav>
  <div class="btn" style="left:990px;top:46px;width:95px;height:36px">MARIT</div>
</header>

<section class="hero">
  <div class="hero-photo" role="img" aria-label="Black and white portrait of Pieter, smiling, wearing glasses"></div>
  <h1 class="hero-title">VELMOT</h1>
  <p class="hero-intro">Hi I'm Pieter, Advisor KLR.<br>Sed ut perspiciatis unde omnis iste natus sit voluptatem accusantium doloremque.</p>
  <div class="signature" role="img" aria-label="Handwritten signature of Pieter"></div>
</section>

<section>
  <h2 class="section-title" style="top:710px">PERSONAL INFORMATION</h2>
  <p class="lead" style="top:756px">Lorem ipsum dolor sit amet, consectetur adipiscing elit, sed do eiusmod tempor<br>incididunt utabore dolore magna aliqua. Ut enim minim veni.</p>
  <div class="info-card">
    <h3 class="card-title" style="left:76px;top:32px">My Story</h3>
    <p class="story">Sed ut perspiciatis unde omnis iste natus error sit volupt atem accusantium doloremque laudantium, totam rem aperiam, eaque ipsa quae ab illo inventore veritatis et quasi architecto beatae vitacta sunt explicabo.</p>
    <div class="btn" style="left:76px;top:204px;width:116px;height:42px">Read More</div>
    <h3 class="card-title" style="left:542px;top:32px">Personal Information</h3>
    <div class="info-row" style="top:72px">Name<span>Pieter</span></div>
    <div class="info-row" style="top:106px">Age<span>52</span></div>
    <div class="info-row" style="top:140px">Phone<span>(+1) 555 010 0100</span></div>
    <div class="info-row" style="top:174px">Email<span>info@velmot.nl</span></div>
    <div class="info-row" style="top:208px">Education<span>Kestra (RA), Lyceum B.</span></div>
    <div class="dots"><i></i><i></i><i></i><i></i></div>
  </div>
</section>

<section class="job">
  <h2 class="section-title" style="top:52px">JOB</h2>
  <p class="lead" style="top:96px">Lorem ipsum dolor sit amet, consectetur adipiscing elit, sedo eiusmod tempor incididunt ut<br>labore dolore magna aliqua veniam, quis exercitation ullamco laboris.</p>
  <svg class="job-icon" style="left:329px;top:196px" width="52" height="50" viewBox="0 0 52 50" fill="none" stroke="#fff" stroke-width="2"><rect x="4" y="4" width="30" height="40"/><line x1="10" y1="14" x2="28" y2="14"/><line x1="10" y1="22" x2="28" y2="22"/><line x1="10" y1="30" x2="22" y2="30"/><line x1="30" y1="42" x2="48" y2="12"/></svg>
  <svg class="job-icon" style="left:634px;top:196px" width="56" height="50" viewBox="0 0 56 50" fill="none" stroke="#fff" stroke-width="2"><circle cx="28" cy="10" r="7"/><polyline points="24,10 27,13 32,7"/><circle cx="14" cy="30" r="5"/><circle cx="28" cy="30" r="5"/><circle cx="42" cy="30" r="5"/><path d="M6 46c0-6 16-6 16 0M20 46c0-6 16-6 16 0M34 46c0-6 16-6 16 0"/></svg>
  <div class="job-text" style="left:329px;top:262px"><strong>ACTUAL JOBS</strong><br>Advisor KLR,<br>Advisor Horizon Partners</div>
  <div class="job-text" style="left:634px;top:262px"><strong>FINISHED JOBS</strong><br>Controller a.i. KLR<br>Advisor Solvera Green, Financial director</div>
</section>

<section>
  <h2 class="skills-title heading">SKILLS</h2>
  <p class="skills-copy" style="top:1752px">At vero eos et accusamus iusto odio dignissimos ducimus qui blandes ditiis praesentium voluptatum deleniti atque corrupti quos dolores et quas molestias quidem rerum facilis est expedit.</p>
  <p class="skills-copy" style="top:1852px">At vero eos et accusamus et iusto odio dignissimos ducimus qui blant ditiis praesentium voluptatum deleniti atque corrupti quos dolores et quas molestias excepturi sint occaecati cupiditate non provident, simi ilique sunt in culpa qui officia deserunt mollitia animi.</p>

  <div class="skill" style="top:1716px"><label>General Management</label><div class="track"><div class="fill" style="width:80%"></div><div class="tag" style="left:247px">80%</div></div></div>
  <div class="skill" style="top:1754px"><label>Energy knowledge</label><div class="track"><div class="fill" style="width:50%"></div><div class="tag" style="left:157px">50%</div></div></div>
  <div class="skill" style="top:1792px"><label>Gas knowledge</label><div class="track"><div class="fill" style="width:95%"></div><div class="tag" style="left:310px">95%</div></div></div>
  <div class="skill" style="top:1830px"><label>People management</label><div class="track"><div class="fill" style="width:50%"></div><div class="tag" style="left:157px">50%</div></div></div>
  <div class="skill" style="top:1868px"><label>Project management</label><div class="track"><div class="fill" style="width:50%"></div><div class="tag" style="left:157px">50%</div></div></div>
  <div class="skill" style="top:1906px"><label>Team player</label><div class="track"><div class="fill" style="width:75%"></div><div class="tag" style="left:247px">75%</div></div></div>
  <div class="skill" style="top:1944px"><label>Trouble shooter</label><div class="track"><div class="fill" style="width:75%"></div><div class="tag" style="left:247px">75%</div></div></div>
</section>

<section class="experience">
  <h2 class="section-title" style="top:126px">EXPERIENCE</h2>
</section>
<div class="exp-row" style="left:195px;top:2239px;width:768px"></div>
<div class="exp-row" style="left:286px;top:2406px;width:765px"></div>
<div class="exp-row" style="left:195px;top:2589px;width:768px"></div>
<div class="exp-row" style="left:286px;top:2757px;width:765px"></div>
<div class="timeline"></div>

<p class="exp-copy" style="left:215px;top:2253px;text-align:right">At vero eos et accusamus et iusto odio dignissimos duci mus qui blanditiis praesentium voluptatum deleniti atque corrupti quos dolores et quas molestias excepturi sintai, officia deserunt mollitia animi, id estorum fuga.</p>
<div class="exp-head" style="left:660px;top:2262px"><h4>2016-PRESENT</h4><p>Quibusdam et aut officiis debitis aut rerum necessitatibus</p></div>
<div class="dot" style="left:603px;top:2257px">1</div>

<div class="exp-head" style="left:272px;top:2434px;text-align:right"><h4>2013-2016</h4><p>Quibusdam et aut officiis debitis aut rerum necessitatibus</p></div>
<p class="exp-copy" style="left:662px;top:2422px">At vero eos et accusamus et iusto odio dignissimos duci mus qui blanditiis praesentium voluptatum deleniti atque corrupti quos dolores et quas molestias excepturi sintai, officia deserunt mollitia animi, id estorum fuga.</p>
<div class="dot" style="left:603px;top:2431px">2</div>

<p class="exp-copy" style="left:215px;top:2603px;text-align:right">At vero eos et accusamus et iusto odio dignissimos duci mus qui blanditiis praesentium voluptatum deleniti atque corrupti quos dolores et quas molestias excepturi sintai, officia deserunt mollitia animi, id estorum fuga.</p>
<div class="exp-head" style="left:660px;top:2612px"><h4>2000-2013</h4><p>Quibusdam et aut officiis debitis aut rerum necessitatibus</p></div>
<div class="dot" style="left:603px;top:2608px">3</div>

<div class="exp-head" style="left:272px;top:2785px;text-align:right"><h4>1990-2000</h4><p>Quibusdam et aut officiis debitis aut rerum necessitatibus</p></div>
<p class="exp-copy" style="left:676px;top:2773px">At vero eos et accusamus et iusto odio dignissimos duci mus qui blanditiis praesentium voluptatum deleniti atque corrupti quos dolores et quas molestias excepturi sintai, officia deserunt mollitia animi, id estorum fuga.</p>
<div class="dot" style="left:603px;top:2781px">4</div>

<section class="partner">
  <div class="partner-photo" role="img" aria-label="Round portrait photo of partner Marit"></div>
  <p class="abs heading" style="left:177px;top:340px;width:248px;text-align:center;font-size:16px;font-weight:600">Marit</p>
  <h2 class="abs" style="left:506px;top:76px;font-size:28px;font-weight:500">MY PARTNER</h2>
  <p class="abs" style="left:506px;top:128px;width:606px;font-size:12.5px;line-height:28px">Sed ut perspiciatis unde omnis iste natus error sit volupt atem accusantium dolor emque laudantium, totam rem aperiam, eaque ipsa quaeb aillo inventore verit atis etus quasi architecto beatae vitacta sunt explicabo. cletates autas except auri, officia deseru mollitia animi usamus dignissimos ducimus quai blan ditiis praesentium voluptatum incididunt utabore dolore.</p>
  <div class="btn" style="left:506px;top:305px;width:116px;height:42px">Read More</div>
</section>

<section>
  <h2 class="section-title" style="top:3572px">PORTFOLIO</h2>
  <svg class="arrow" style="left:52px" width="14" height="20" viewBox="0 0 14 20"><polyline points="11,2 3,10 11,18" fill="none" stroke="#1f1f1f" stroke-width="2"/></svg>
  <div class="folio" style="left:113px;background:linear-gradient(135deg,#8a6a52,#c9b8a6 55%,#efe9e2)" role="img" aria-label="Portfolio photo: hands working on financial charts at a desk"></div>
  <div class="folio" style="left:359px;background:linear-gradient(135deg,#6b6058,#d8d4cf 50%,#9a8d82)" role="img" aria-label="Portfolio photo: business meeting reviewing printed reports"></div>
  <div class="folio" style="left:606px;background:linear-gradient(135deg,#5b6c7a,#dde3e8 55%,#a7b3bd)" role="img" aria-label="Portfolio photo: tablet and documents with charts"></div>
  <div class="folio" style="left:853px;background:linear-gradient(135deg,#c28a4e,#e8d3b8 55%,#7c6450)" role="img" aria-label="Portfolio photo: team pointing at graphs on paper"></div>
  <svg class="arrow" style="left:1139px" width="14" height="20" viewBox="0 0 14 20"><polyline points="3,2 11,10 3,18" fill="none" stroke="#1f1f1f" stroke-width="2"/></svg>
</section>

<section class="work">
  <h2 class="section-title" style="top:62px;font-size:26px">PIETER WORK</h2>
  <p class="abs heading" style="left:0;top:110px;width:1200px;text-align:center;font-size:19px;font-weight:600">Worked For - Brenner Advocaten &amp; Notarissen Halvorsen</p>
  <p class="lead" style="top:150px">Lorem ipsum dolor sit amet, consectetur adipiscing elit, sed do eiusmod tempor incididunt ut labore dolore<br>magna aliqua veniam, quis nostrud exercitation ullamco laboris.</p>
</section>

<footer>
  <div class="logo" style="left:113px;top:4338px"><span>VELMOT</span><span class="mark"></span></div>
  <h4 class="foot-title" style="left:326px;top:4286px">Quick links</h4>
  <ul class="foot-list" style="left:326px;top:4311px">
    <li>About Me</li><li>Experience</li><li>Skills</li><li>Portfolio</li><li>Contact</li>
  </ul>
  <h4 class="foot-title" style="left:560px;top:4286px">Social Link</h4>
  <ul class="foot-list" style="left:560px;top:4311px">
    <li><span class="pip"></span>Facebook</li><li><span class="pip"></span>Twitter</li><li><span class="pip"></span>Linked</li><li><span class="pip"></span>Instagram</li>
  </ul>
  <h4 class="foot-title" style="left:798px;top:4286px">Subscribe Newsletter</h4>
  <div class="input">Enter the Email</div>
  <div class="btn" style="left:798px;top:4383px;width:116px;height:38px">Subscribe</div>
  <div class="rule"></div>
  <p class="copyright">Copyrights © 2018 All rights reserved</p>
</footer>

</body>
</html>
```